Letterhead designs for Property Management firm

Would like to see some different letterhead/envelope designs We are a residential property management company. We would like to see designs that utilize blue/grays/black

```html
<!DOCTYPE html>
<html lang="en">
<head>
<meta charset="utf-8">
<title>Harborview Property Management Letterhead</title>
<link href="https://fonts.googleapis.com/css2?family=Arimo:wght@400;700&display=swap" rel="stylesheet">
<style>
  :root {
    --backdrop: #2a2c30;
    --paper: #ffffff;
    --ink: #5a5c60;
    --ink-strong: #4a4c50;
    --brand-blue: #1d4f9e;
    --brand-dark: #1c1d20;
    --signature-tone: #e4e6ea;
  }
  * { box-sizing: border-box; margin: 0; padding: 0; }
  html, body {
    width: 1200px; height: 1200px; overflow: hidden;
    background: var(--backdrop);
    font-family: "Arimo", Arial, sans-serif;
  }
  .letterhead {
    position: absolute; left: 200px; top: 35px;
    width: 800px; height: 1130px;
    background: var(--paper);
    color: var(--ink);
    font-size: 13.4px; line-height: 18.8px;
  }
  .brand {
    position: absolute; top: 60px; left: 0; width: 100%;
    display: flex; justify-content: center; align-items: center; gap: 10px;
  }
  .brand-mark {
    width: 14px; height: 14px; background: var(--brand-blue);
  }
  .brand-name {
    color: var(--brand-blue); font-weight: 700;
    font-size: 22px; line-height: 26px; letter-spacing: 0.5px;
    text-transform: uppercase; text-align: center;
  }
  .letter-body {
    position: absolute; left: 84px; top: 263px; width: 634px;
  }
  .date { margin-bottom: 37px; }
  .recipient { margin-bottom: 19px; }
  .recipient .name, .closing .title { font-weight: 700; color: var(--ink-strong); }
  .salutation { margin-bottom: 19px; }
  .letter-body p.copy { text-align: justify; margin-bottom: 18.8px; }
  .closing { margin-top: 37px; }
  .signature {
    display: block; width: 180px; height: 22px; margin: -4px 0 0 0;
    background: linear-gradient(90deg, var(--signature-tone), rgba(228,230,234,0.2));
    border-radius: 3px;
  }
  .footer-box {
    position: absolute; left: 125px; top: 1058px; width: 550px; height: 40px;
    border: 2px solid var(--brand-blue); border-bottom: none;
    font-size: 13.4px; text-align: center; padding-top: 10px;
  }
  .footer-box .firm { color: var(--brand-blue); font-weight: 700; }
  .contact-line {
    position: absolute; left: 123px; top: 1090px; width: 554px;
    display: flex; align-items: center; gap: 8px;
    font-size: 13.4px; color: var(--ink);
  }
  .contact-line .rule { flex: 1; height: 2px; background: var(--brand-blue); }
  .contact-line .item { display: inline-flex; align-items: center; gap: 5px; white-space: nowrap; }
  .contact-line .sep { color: var(--ink); }
  .contact-line svg { width: 10px; height: 10px; }
</style>
</head>
<body>
  <main class="letterhead">
    <header class="brand">
      <span class="brand-mark"></span>
      <span class="brand-name">Harborview<br>Property Management</span>
    </header>

    <section class="letter-body">
      <div class="date">January 1, 2050</div>
      <div class="recipient">
        <div class="name">Daniel Reeves</div>
        <div>Managing Director</div>
        <div>Co.Street, Building/Suite</div>
        <div>City/State, Zip Code</div>
      </div>
      <div class="salutation">Dear Thomas Whitfield,</div>
      <p class="copy">Lorem ipsum dolor sit amet, consectetuer adipiscing elit, sed diam nonummy nibh euismod tincidunt ut laoreet dolore magna aliquam erat volutpat. Ut wisi enim ad minim veniam, quis nostrud exerci tation ullamcorper suscipit lobortis nisl ut aliquip ex ea commodo consequat. Duis dolore te feugait nulla facilisi. Nam liber tempor cum soluta nobis eleifend option congue nihil imperdiet doming id quod mazim placerat facer possim assum. Lorem ipsum dolor sit amet, consectetuer adipiscing elit, sed diam nonummy nibh euismod tincidunt ut laoreet dolore magna aliquam erat volutpat. Ut wisi enim ad minim veniam, quis nostrud exerci tation ullamcorper suscipit lobortis nisl ut aliquip ex ea commodo consequat.</p>
      <p class="copy">Consectetuer adipiscing elit, sed diam nonummy nibh euismod tincidunt ut laoreet dolore magna aliquam erat volutpat. Ut wisi enim ad minim veniam, quis nostrud exerci tation ullamcorper suscipit lobortis nisl ut aliquip ex ea commodo consequat. Consectetuer adipiscing elit, sed diam nonummy nibh euismod tincidunt ut laoreet dolore magna aliquam erat volutpat. Ut wisi enim ad minim veniam, quis nostrud exerci tation ullamcorper suscipit lobortis nisl ut aliquip ex ea commodo consequat.</p>
      <p class="copy">Duis dolore te feugait nulla facilisi. Nam liber tempor cum soluta nobis eleifend option congue nihil imperdiet doming id quod mazim placerat facer possim assum.Duis dolore te feugait nulla facilisi. Nam liber tempor cum soluta nobis eleifend option congue nihil imperdiet doming id quod mazim placerat facer possim assum.</p>
      <div class="closing">
        <div>Sincerely Yours,</div>
        <span class="signature" role="img" aria-label="Handwritten signature of the managing director"></span>
        <div class="title">Authorized Managing Director</div>
        <div>Your Company Name</div>
      </div>
    </section>

    <footer>
      <div class="footer-box">
        <span class="firm">Harborview Property Management,</span> Co.Street, Building/Suite 12345, City/State, Zip Code
      </div>
      <div class="contact-line">
        <span class="rule"></span>
        <span class="item">
          <svg viewBox="0 0 10 10" aria-hidden="true"><path d="M2 0.5 L3.8 2.6 L2.9 3.7 Q4 6 6.3 7.1 L7.4 6.2 L9.5 8 L8.2 9.5 Q1 8.5 0.5 1.8 Z" fill="var(--brand-blue)"/></svg>
          310.555.0142
        </span>
        <span class="sep">|</span>
        <span class="item">
          <svg viewBox="0 0 10 10" aria-hidden="true"><rect x="0.6" y="2" width="8.8" height="6" fill="none" stroke="var(--brand-blue)" stroke-width="1"/><path d="M0.6 2 L5 5.5 L9.4 2" fill="none" stroke="var(--brand-blue)" stroke-width="1"/></svg>
          info@harborviewproperty.com
        </span>
        <span class="sep">|</span>
        <span class="item">
          <svg viewBox="0 0 10 10" aria-hidden="true"><circle cx="5" cy="5" r="4.4" fill="none" stroke="var(--brand-blue)" stroke-width="1"/><path d="M0.6 5 H9.4 M5 0.6 Q2.5 5 5 9.4 M5 0.6 Q7.5 5 5 9.4" fill="none" stroke="var(--brand-blue)" stroke-width="0.8"/></svg>
          www.harborviewproperty.com
        </span>
        <span class="rule"></span>
      </div>
    </footer>
  </main>
</body>
</html>
```